Business Cards, Letterhead, Envelopes etc.
Need design that fits with tech saavy customers
Business Cards, Letterhead, Envelopes etc.  -
Creative Brief
Use specific fonts
Use same font or one that works with the logo
Cutting-Edge
Dean R. Marlow
President
418 Bellwick Street Palo Alto, CA 94306
dean@quevrafin.com
quevrafin.com
CA DRE: #00471362, NMLS: #517294
Need design for business cards, letterhead, #10 envelopes and mailing labels for package shipments.

```html
<!DOCTYPE html>
<html lang="en">
<head>
<meta charset="utf-8">
<title>Quevrafin Stationery Set</title>
<link rel="stylesheet" href="https://fonts.googleapis.com/css2?family=Open+Sans:wght@400;600;700&display=swap">
<style>
  :root{
    --backdrop:#a7a7a7;
    --paper:#ffffff;
    --brand-blue:#2a63b3;
    --ink:#3a3a3a;
    --muted:#777777;
    --flap:#2f66b5;
  }
  *{margin:0;padding:0;box-sizing:border-box}
  html,body{width:1200px;height:626px;overflow:hidden}
  body{background:var(--backdrop);font-family:"Open Sans",Arial,sans-serif;color:var(--ink);position:relative}
  .sheet{position:absolute;background:var(--paper);box-shadow:0 1px 3px rgba(0,0,0,.25)}
  .brand-name{font-family:"Open Sans",Arial,sans-serif;font-weight:700;color:var(--brand-blue);letter-spacing:-0.5px;line-height:1}

  /* Letterhead */
  .letterhead{left:192px;top:79px;width:396px;height:533px}
  .letterhead .stripe{position:absolute;left:43px;top:0;width:11px;height:100%;background:var(--brand-blue)}
  .letterhead .brand-name{position:absolute;left:70px;top:22px;font-size:27px}
  .letter-body{position:absolute;left:70px;top:88px;width:300px;font-size:5.6px;line-height:1.5}
  .letter-body p{margin-bottom:6px}
  .letter-body .recipient{font-weight:600;margin-bottom:12px;font-size:6px}
  .signature{width:80px;height:26px;margin:6px 0 4px;background:linear-gradient(90deg,#444 0%,#666 100%);opacity:.35;border-radius:12px}
  .letter-footer{position:absolute;left:70px;bottom:14px;width:310px;font-size:5px;line-height:1.7;color:var(--muted)}
  .letter-footer .web{position:absolute;right:0;bottom:0;color:var(--ink)}
  .contact-line{display:flex;align-items:center;gap:3px}
  .contact-line svg{width:5px;height:5px;fill:var(--brand-blue)}

  /* Business card */
  .business-card{left:17px;top:295px;width:163px;height:94px}
  .business-card .stripe{position:absolute;left:0;top:0;width:7px;height:100%;background:var(--brand-blue)}
  .card-person{position:absolute;left:14px;top:10px;font-size:5.5px;line-height:1.4}
  .card-person strong{font-weight:700;font-size:6px}
  .business-card .brand-name{position:absolute;left:14px;top:38px;font-size:18px}
  .card-contact{position:absolute;left:14px;bottom:8px;font-size:4.4px;line-height:1.5;color:var(--muted)}

  /* Envelope back */
  .envelope-back{left:636px;top:161px;width:545px;height:180px;overflow:hidden}
  .envelope-back svg{position:absolute;inset:0}

  /* Envelope front */
  .envelope-front{left:679px;top:336px;width:502px;height:230px}
  .envelope-front .stripe{position:absolute;left:24px;top:0;width:6px;height:100%;background:var(--brand-blue)}
  .envelope-front .brand-name{position:absolute;left:38px;top:24px;font-size:24px}
  .return-address{position:absolute;left:38px;top:190px;font-size:4.6px;line-height:1.6;color:var(--muted)}
  .envelope-front .web{position:absolute;right:20px;bottom:14px;font-size:5px;color:var(--ink)}
</style>
</head>
<body>

<section class="sheet letterhead" aria-label="Letterhead">
  <div class="stripe"></div>
  <div class="brand-name">QUEVRAFIN</div>
  <div class="letter-body">
    <p class="recipient">Lucas Rivera<br>Office of Lending<br>Upland Terrace, Suite 4</p>
    <p>Dear Lucas,</p>
    <p>Thank you for choosing our team to guide your home financing. We review every file with care, compare current rates across many lenders, and explain each step in plain terms so you always know where your loan stands.</p>
    <p>Our online portal lets you upload documents, sign forms and track approvals from any device. Updates arrive by email the moment something changes, and a dedicated advisor is ready to answer questions during business hours or by appointment.</p>
    <p>Enclosed you will find a summary of the options we discussed, including estimated monthly payments, closing costs and timelines. Please review it at your convenience and let us know which path fits your plans best.</p>
    <p>We look forward to helping you reach your goals.</p>
    <p>Sincerely yours,</p>
    <div class="signature" role="img" aria-label="Handwritten signature"></div>
    <p>Dean R. Marlow</p>
  </div>
  <div class="letter-footer">
    <div class="contact-line"><svg viewBox="0 0 10 10"><circle cx="5" cy="5" r="5"/></svg>418 Bellwick Street Palo Alto, CA 94306</div>
    <div class="contact-line"><svg viewBox="0 0 10 10"><circle cx="5" cy="5" r="5"/></svg>(650) 555-0142</div>
    <div class="contact-line"><svg viewBox="0 0 10 10"><circle cx="5" cy="5" r="5"/></svg>dean@quevrafin.com</div>
    <div class="contact-line"><svg viewBox="0 0 10 10"><circle cx="5" cy="5" r="5"/></svg>CA DRE: #00471362, NMLS: #517294</div>
    <div class="web">quevrafin.com</div>
  </div>
</section>

<section class="sheet business-card" aria-label="Business card">
  <div class="stripe"></div>
  <div class="card-person"><strong>Dean R. Marlow</strong><br>President</div>
  <div class="brand-name">QUEVRAFIN</div>
  <div class="card-contact">
    418 Bellwick Street Palo Alto, CA 94306<br>
    dean@quevrafin.com · quevrafin.com<br>
    CA DRE: #00471362, NMLS: #517294
  </div>
</section>

<section class="sheet envelope-back" aria-label="Envelope back">
  <svg viewBox="0 0 545 180" preserveAspectRatio="none">
    <polygon points="0,0 545,0 545,10 300,98 245,98 0,10" fill="var(--flap)"/>
    <line x1="0" y1="180" x2="272" y2="100" stroke="#e4e4e4" stroke-width="1"/>
    <line x1="545" y1="180" x2="272" y2="100" stroke="#e4e4e4" stroke-width="1"/>
  </svg>
</section>

<section class="sheet envelope-front" aria-label="Envelope front">
  <div class="stripe"></div>
  <div class="brand-name">QUEVRAFIN</div>
  <div class="return-address">
    418 Bellwick Street<br>
    Palo Alto, CA 94306<br>
    dean@quevrafin.com
  </div>
  <div class="web">quevrafin.com</div>
</section>

</body>
</html>
```